Form Sculptors Business Card

Professional cosmetic surgery company, based in very exclusive area in London. High profiled clientele. Brand is very artistic, modern, state-of-the-art, safe. The best in the business. Celebrity clientele.

Form Sculptor’s of London is a brand serving a discriminating and exclusive clientele who value personal service that is both intimate and high end. Our clients choose Form Sculptors because of the relationships we share with all of our customers. The clients of Form Sculptors have an equal partnership between customers, and very experienced, highly qualified medical professionals. This together provides you with a professional service that keeps you looking good and feeling good. It is a relationship based on honesty, compassion, loyalty and respect.
Form Sculptor’s have provided services for internationally recognised celebrities, and other high profiled individuals.

The cards are used for networking at private, exclusive events with VIPs.

Target Market(s)

Professionals
Rich people

Industry/Entity Type

Professional Service

Contact Information for Business Card

Need double sided business card design for 4 people. Back of the business card needs to have contrast background to the front with butterfly watermark with services provided:
Hair Restoration surgery
Hair Loss treatments
Breast surgery
Rhinoplasty
Pulvix Liposuction
Fat Grafting
Lumaxin & Fillers

Front of the business card needs to be a nice satin black.
with following information:
Calvert Osterlund - name
Chief Executive - Job title

www.formsculptors-example.co.uk
calvert@formsculptors-example.co.uk
Phone: +44 (0)207 946 0321
Mobile: +44 (0)7700 900 147

The London Farrowmere Clinic
14 Farrowmere Lane | London | W1X 4QP
Off Quenby Street

All business cards have the same address, phone, website as Calvert's details.
Same details on the back of the business card as well.
The other cards have different name, job title, email, mobile number

Teodor Lunn - Name
Partner - Job Title
Former England International Cricketer - please include below job title

email: teodor@formsculptors-example.co.uk
mobile: +44(0)7700 900582

Dr Castello Vranesk - Name
Plastic Surgeon - Job Title
drvranesk@formsculptors-example.co.uk
No mobile number

Dr Ezra Tolquist FRCS (please put FRCS in small font) - Name
Hair Restoration Surgeon - Job Title
drtolquist@formsculptors-example.co.uk
No mobile number

Colors
cedeec
85abd2
0655a3

Requirements
Must have
• The logo needs to be in a metallic finish
• Text needs to be striking
• nice background
• butterfly watermark on the back

```html
<!DOCTYPE html>
<html lang="en">
<head>
<meta charset="utf-8">
<title>Form Sculptors Business Card</title>
<link href="https://fonts.googleapis.com/css2?family=Lato:wght@400;700;900&display=swap" rel="stylesheet">
<style>
  :root {
    --page: #e6e6e8;
    --card: #3a393c;
    --card-deep: #333235;
    --blue: #2a8fd0;
    --blue-deep: #0655a3;
    --white: #ffffff;
    --ink-soft: #e4e4e6;
    --mark: #6f6e72;
  }
  * { margin: 0; padding: 0; box-sizing: border-box; }
  html, body {
    width: 1000px; height: 1200px; overflow: hidden;
    background: var(--page);
    font-family: "Lato", Arial, sans-serif;
  }
  .sheet {
    position: relative; width: 1000px; height: 1200px;
    display: flex; flex-direction: column; align-items: center; justify-content: center; gap: 44px;
  }
  .card {
    position: relative; width: 880px; height: 520px;
    background: linear-gradient(160deg, var(--card) 0%, var(--card-deep) 100%);
    box-shadow: 0 10px 28px rgba(0,0,0,.28);
    overflow: hidden;
  }

  /* Front */
  .brand {
    position: absolute; left: 120px; top: 246px;
    display: flex; align-items: center; gap: 14px;
  }
  .brand-dot { width: 26px; height: 26px; border-radius: 50%; background: var(--blue); }
  .brand-name {
    font-weight: 700; font-size: 40px; color: var(--blue); letter-spacing: 1px;
  }
  .name-band {
    position: absolute; left: 505px; top: 114px; right: 0; height: 89px;
    background: var(--blue);
    padding: 14px 0 0 26px; color: var(--white);
  }
  .divider {
    position: absolute; left: 502px; top: 88px; width: 4px; height: 360px;
    background: linear-gradient(to bottom, rgba(0,0,0,0), rgba(0,0,0,.45) 30%, rgba(0,0,0,.45) 70%, rgba(0,0,0,0));
  }
  .person-name { font-size: 27px; line-height: 32px; letter-spacing: .3px; }
  .person-name .first { font-weight: 900; }
  .person-name .last { font-weight: 400; }
  .person-title { font-size: 19px; line-height: 24px; font-weight: 400; letter-spacing: .6px; }

  .contacts { position: absolute; left: 505px; top: 236px; list-style: none; }
  .contact {
    position: relative; display: flex; align-items: flex-start;
    height: 46px; color: var(--ink-soft); font-size: 19px; line-height: 24px;
  }
  .contact.address { height: 60px; }
  .contact-tab {
    position: absolute; left: 0; top: 8px; width: 22px; height: 16px; background: var(--blue);
  }
  .contact-icon {
    position: relative; margin-left: 14px; width: 34px; height: 34px; flex: none;
    border-radius: 50%; background: var(--blue);
    display: flex; align-items: center; justify-content: center;
  }
  .contact-icon svg { width: 26px; height: 26px; }
  .contact-text { margin-left: 18px; padding-top: 4px; }

  /* Back */
  .frame {
    position: absolute; left: 71px; top: 70px; width: 729px; height: 371px;
    border: 2px solid var(--blue);
  }
  .watermark {
    position: absolute; left: 0; right: 0; top: 200px; text-align: center;
    font-weight: 700; font-size: 64px; color: var(--mark); letter-spacing: 2px;
  }
  .site-url {
    position: absolute; left: 50%; top: 427px; transform: translateX(-50%);
    background: var(--card-deep); padding: 0 22px;
    color: var(--white); font-weight: 700; font-size: 19px; letter-spacing: 2px; white-space: nowrap;
  }
</style>
</head>
<body>
<main class="sheet">

  <section class="card card-front" aria-label="Business card front">
    <div class="brand">
      <span class="brand-dot"></span>
      <span class="brand-name">Form Sculptors</span>
    </div>

    <div class="divider"></div>
    <div class="name-band">
      <p class="person-name"><span class="first">CALVERT</span> <span class="last">OSTERLUND</span></p>
      <p class="person-title">CHIEF EXECUTIVE</p>
    </div>

    <ul class="contacts">
      <li class="contact">
        <span class="contact-tab"></span>
        <span class="contact-icon">
          <svg viewBox="0 0 26 26"><circle cx="13" cy="13" r="12" fill="#3a393c"/><path d="M7 11c0-2 3-3 6-3s6 1 6 3v1h-3v-1h-6v1H7z M9 13h8l1 5H8z" fill="#fff"/></svg>
        </span>
        <span class="contact-text">+44 (0)207 946 0321</span>
      </li>
      <li class="contact">
        <span class="contact-tab"></span>
        <span class="contact-icon">
          <svg viewBox="0 0 26 26"><circle cx="13" cy="13" r="12" fill="#3a393c"/><rect x="6.5" y="8.5" width="13" height="9" fill="#fff"/><path d="M6.5 8.5l6.5 5 6.5-5" fill="none" stroke="#3a393c" stroke-width="1.2"/></svg>
        </span>
        <span class="contact-text">calvert@formsculptors-example.co.uk</span>
      </li>
      <li class="contact">
        <span class="contact-tab"></span>
        <span class="contact-icon">
          <svg viewBox="0 0 26 26"><circle cx="13" cy="13" r="12" fill="#3a393c"/><g fill="none" stroke="#fff" stroke-width="1.3"><circle cx="13" cy="13" r="6.5"/><ellipse cx="13" cy="13" rx="3" ry="6.5"/><path d="M6.5 13h13M7.5 10h11M7.5 16h11"/></g></svg>
        </span>
        <span class="contact-text">www.formsculptors-example.co.uk</span>
      </li>
      <li class="contact address">
        <span class="contact-tab"></span>
        <span class="contact-icon">
          <svg viewBox="0 0 26 26"><circle cx="13" cy="13" r="12" fill="#3a393c"/><path d="M6 13.5L13 7l7 6.5h-2V19h-3.5v-4h-3v4H8v-5.5z" fill="#fff"/></svg>
        </span>
        <span class="contact-text">The London Farrowmere Clinic<br>14 Farrowmere Lane</span>
      </li>
    </ul>
  </section>

  <section class="card card-back" aria-label="Business card back">
    <div class="frame"></div>
    <p class="watermark">Form Sculptors</p>
    <p class="site-url">WWW.FORMSCULPTORS-EXAMPLE.CO.UK</p>
  </section>

</main>
</body>
</html>
```